Website for new dental office

I am Dr. Colin Ashford and am building a new dental practice. I specialize in general dentistry. I am young and have a higher end dental practice incorporating very new technologies and would like my website to reflect that. As many dental patients are older, the website must be very easy to navigate. I would like patients to be able to request appointments, and will eventually add on patient information forms (the health history, etc, that you normally fill out in the practice) from my practice management software, so leave an area for that.

Industry/Entity Type

Building

```html
<!DOCTYPE html>
<html lang="en">
<head>
<meta charset="utf-8">
<title>Ashford Dental Clinic</title>
<link href="https://fonts.googleapis.com/css2?family=Open+Sans:wght@400;600&family=Arimo:wght@400&display=swap" rel="stylesheet">
<style>
:root{
  --ink:#222;
  --body:#555;
  --brand:#2a9ad6;
  --nav-top:#7fd0f2;
  --nav-bot:#4db8e8;
  --nav-active:#333;
  --dark:#1c1c1c;
  --footer:#232323;
  --band-top:#f2f6f8;
  --band-bot:#cfe0ea;
  --btn:#2b7fc4;
  --btn-dark:#1f5f97;
  --line:#c9c9c9;
  --box:#e9edef;
}
*{box-sizing:border-box;margin:0;padding:0}
html,body{width:836px;height:1200px;overflow:hidden;background:#fff}
body{position:relative;font-family:"Arimo",Arial,sans-serif;color:var(--ink)}
.abs{position:absolute}
.topbar{left:0;top:0;width:836px;height:14px;background:var(--dark)}
.brand{left:117px;top:33px;display:flex;align-items:center;gap:8px}
.brand-mark{width:38px;height:38px;border-radius:50%;background:#e3f2fa}
.brand-name{font-family:"Open Sans",sans-serif;font-size:21px;color:var(--ink)}
.call{left:548px;top:47px;display:flex;align-items:center;gap:8px;font-family:"Open Sans",sans-serif;font-size:12.5px;color:var(--brand)}
.nav{left:0;top:89px;width:836px;height:37px;background:linear-gradient(var(--nav-top),var(--nav-bot))}
.nav ul{list-style:none;display:flex;position:absolute;left:119px;top:0;height:37px}
.nav li{font-family:"Open Sans",sans-serif;font-size:10.8px;color:#fff;padding:0 12px;line-height:37px;border-right:1px solid rgba(255,255,255,.35)}
.nav li:last-child{border-right:none}
.nav li.active{background:var(--nav-active);padding:0 10px}
.hero{left:0;top:126px;width:836px;height:400px;background:linear-gradient(100deg,#cfd6dc 0%,#e9e4e0 35%,#f3f1ef 55%,#c9d6df 80%,#aebdc9 100%)}
.caption{left:365px;top:391px;width:350px;height:77px;background:rgba(40,40,40,.82);color:#fff;font-family:"Open Sans",sans-serif;font-size:16px;line-height:30px;text-align:center;padding-top:9px;white-space:nowrap;overflow:hidden}
.dots{left:659px;top:477px;display:flex;gap:3px}
.dots span{width:11px;height:11px;border-radius:50%;border:2px solid #fff;background:rgba(255,255,255,.2)}
.band{left:0;top:526px;width:836px;height:72px;background:linear-gradient(var(--band-top),var(--band-bot))}
.band p{position:absolute;left:130px;top:28px;font-size:13.6px;color:var(--ink)}
.register{position:absolute;left:586px;top:20px;width:116px;height:33px;background:linear-gradient(#62c4ee,#3ba9e0);color:#fff;font-family:"Open Sans",sans-serif;font-size:12px;line-height:33px;text-align:center;border-radius:2px}
.col{top:620px;width:182px}
.col h2{font-family:"Arimo",Arial,sans-serif;font-weight:400;font-size:14.5px;line-height:18px;color:var(--ink)}
.col-icon{position:absolute;top:0;right:0;width:52px;height:52px;border-radius:50%;background:radial-gradient(#fff 55%,#e2e6e8)}
.col-icon svg{position:absolute;left:14px;top:14px}
.col p{font-size:8.6px;line-height:14px;color:var(--body);text-align:justify}
.photo{width:182px;height:85px;background:linear-gradient(90deg,#8aa9b8,#c9dbe4 50%,#e8d9c8)}
.btn{display:inline-block;height:20px;padding:0 8px;background:linear-gradient(#3f95d6,var(--btn));border:1px solid var(--btn-dark);color:#fff;font-family:"Open Sans",sans-serif;font-weight:600;font-size:8.4px;line-height:18px;border-radius:2px}
.services{list-style:none}
.services li{font-size:8.4px;color:#333;display:flex;align-items:center;gap:12px;height:22px}
.contact-box{width:182px;height:40px;background:var(--box);border:1px solid #cfd5d8;display:flex;align-items:center;gap:9px;padding-left:9px;font-family:"Open Sans",sans-serif;font-size:10.5px;color:#333;white-space:nowrap}
.divider{left:117px;top:924px;width:600px;height:1px;background:var(--line)}
.blog-title{left:117px;top:947px;font-family:"Open Sans",sans-serif;font-size:13px;color:var(--ink)}
.arrows{left:685px;top:946px;display:flex;gap:1px}
.arrows span{width:15px;height:15px;background:#666;display:flex;align-items:center;justify-content:center}
.thumb{top:974px;width:142px;height:96px;border:1px solid #d5d5d5}
.footer{left:0;top:1096px;width:836px;height:104px;background:var(--footer);color:#fff;font-family:"Open Sans",sans-serif}
.footer-links{position:absolute;top:16px;width:836px;text-align:center;font-size:8.8px}
.footer-links span{margin:0 4px}
.social{position:absolute;left:335px;top:45px;display:flex;gap:4px}
.social span{width:24px;height:24px;border-radius:50%;background:#fff}
.copy{position:absolute;top:80px;width:836px;text-align:center;font-size:8.8px}
</style>
</head>
<body>
<div class="abs topbar"></div>

<header>
  <div class="abs brand">
    <span class="brand-mark"></span>
    <span class="brand-name">Ashford Dental Clinic</span>
  </div>
  <div class="abs call">
    <svg width="17" height="17" viewBox="0 0 20 20"><circle cx="10" cy="10" r="10" fill="#111"/><path d="M6.5 5.5c.6-.6 1.3-.5 1.6 0l1 1.6c.3.5.1 1-.3 1.3l-.6.5c.5 1.1 1.4 2 2.5 2.6l.5-.6c.4-.4.9-.5 1.3-.2l1.6 1c.5.3.5 1 0 1.6-.9 1-2.4 1.1-4 .1-2-1.2-3.4-2.8-4.1-4.5-.5-1.300-.3-2.6.5-3.4z" fill="#fff"/></svg>
    <span>CALL US: 1 (800) 555 0142</span>
  </div>
</header>

<nav class="abs nav">
  <ul>
    <li class="active">HOME</li>
    <li>ABOUT US</li>
    <li>MEDICAL SERVICES</li>
    <li>OUR DOCTORS</li>
    <li>APPOINTMENTS</li>
    <li>LOCATIONS</li>
    <li>CONTACT US</li>
  </ul>
</nav>

<section class="abs hero" role="img" aria-label="Photo of a dentist treating a smiling patient in the chair"></section>
<div class="abs caption">DR. COLIN ASHFORD IS SPECIALISED<br>IN GENERAL DENTISTRY</div>
<div class="abs dots"><span></span><span></span><span></span><span></span></div>

<section class="abs band">
  <p>He provides higher end dental practice incorporating very new technologies</p>
  <span class="register">REGISTER NOW</span>
</section>

<section class="abs col" style="left:117px">
  <div class="col-icon"><svg width="24" height="24" viewBox="0 0 24 24"><rect x="3" y="2" width="18" height="20" rx="2" fill="#5bb7e6"/><circle cx="12" cy="9" r="3.5" fill="#fff"/><path d="M6 18c1-3.5 3-5 6-5s5 1.5 6 5z" fill="#fff"/></svg></div>
  <h2>Meet the Staff:<br>Dr. Colin Ashford</h2>
  <p style="margin-top:20px">Sed ut perspiciatis unde omnis iste natus error sit voluptatem accusantium doloreue laudantium, totam rem aperiam.</p>
  <div class="photo" role="img" aria-label="Photo of the dentist with a smiling patient" style="margin-top:6px"></div>
  <p style="margin-top:10px">Eaque ipsa quae ab illo inventore veritatis et quasi architecto beatae vitae dicta sunt explicabo, perspiciatis unde omnis.</p>
  <span class="btn" style="margin-top:12px">READ MORE</span>
</section>

<section class="abs col" style="left:328px">
  <div class="col-icon"><svg width="24" height="24" viewBox="0 0 24 24"><path d="M9 2h6v7h7v6h-7v7H9v-7H2V9h7z" fill="#4fb1e4"/></svg></div>
  <h2>Check out our<br>Medical Services</h2>
  <p style="margin-top:20px;text-align:left">Our most important medical departments, but just a few of what our clinic offers:</p>
  <ul class="services" style="margin-top:6px">
    <li><svg width="10" height="10" viewBox="0 0 10 10"><circle cx="5" cy="5" r="5" fill="#4aa9df"/><path d="M2.6 5.1l1.6 1.6 3.2-3.3" stroke="#fff" stroke-width="1.3" fill="none"/></svg>Cardiothoracic Surgery</li>
    <li><svg width="10" height="10" viewBox="0 0 10 10"><circle cx="5" cy="5" r="5" fill="#4aa9df"/><path d="M2.6 5.1l1.6 1.6 3.2-3.3" stroke="#fff" stroke-width="1.3" fill="none"/></svg>Cardiovascular Diseases</li>
    <li><svg width="10" height="10" viewBox="0 0 10 10"><circle cx="5" cy="5" r="5" fill="#4aa9df"/><path d="M2.6 5.1l1.6 1.6 3.2-3.3" stroke="#fff" stroke-width="1.3" fill="none"/></svg>Ophthalmology</li>
    <li><svg width="10" height="10" viewBox="0 0 10 10"><circle cx="5" cy="5" r="5" fill="#4aa9df"/><path d="M2.6 5.1l1.6 1.6 3.2-3.3" stroke="#fff" stroke-width="1.3" fill="none"/></svg>Dermatology</li>
    <li><svg width="10" height="10" viewBox="0 0 10 10"><circle cx="5" cy="5" r="5" fill="#4aa9df"/><path d="M2.6 5.1l1.6 1.6 3.2-3.3" stroke="#fff" stroke-width="1.3" fill="none"/></svg>General Surgery</li>
    <li><svg width="10" height="10" viewBox="0 0 10 10"><circle cx="5" cy="5" r="5" fill="#4aa9df"/><path d="M2.6 5.1l1.6 1.6 3.2-3.3" stroke="#fff" stroke-width="1.3" fill="none"/></svg>Consultative &amp; Diagnostic Medicine</li>
    <li><svg width="10" height="10" viewBox="0 0 10 10"><circle cx="5" cy="5" r="5" fill="#4aa9df"/><path d="M2.6 5.1l1.6 1.6 3.2-3.3" stroke="#fff" stroke-width="1.3" fill="none"/></svg>Infectious Diseases</li>
  </ul>
  <span class="btn" style="margin-top:10px">READ MORE</span>
</section>

<section class="abs col" style="left:534px">
  <div class="col-icon"><svg width="24" height="24" viewBox="0 0 24 24"><rect x="3" y="4" width="18" height="17" rx="2" fill="#fff" stroke="#8a9aa3"/><rect x="3" y="4" width="18" height="5" fill="#4fb1e4"/><path d="M7 13h3M12 13h3M7 16h3M12 16h3" stroke="#9aa"/></svg></div>
  <h2>Make an<br>Appointment</h2>
  <p style="margin-top:20px">Sed ut perspiciatis unde omnis iste natus error sit voluptatem accusantium doloreue laudantium, totam rem aperiam, eaque ipsa quae ab illo Lorem ipsum dolor sit amet, consectetur et quasi architecto:</p>
  <div class="contact-box" style="margin-top:4px">
    <svg width="12" height="20" viewBox="0 0 12 20"><rect x="1" y="1" width="10" height="18" rx="2" fill="#2a9ad6"/><rect x="3" y="4" width="6" height="10" fill="#fff"/></svg>
    <span>by phone: +33 (0) 5550 1234</span>
  </div>
  <div class="contact-box" style="margin-top:5px">
    <svg width="14" height="10" viewBox="0 0 14 10"><rect width="14" height="10" fill="#2a9ad6"/><path d="M0 0l7 6 7-6" stroke="#fff" fill="none"/></svg>
    <span>by email: mail@ashford.test</span>
  </div>
  <p style="margin-top:10px;text-align:right">...or fill in the form on our Appointments page:</p>
  <span class="btn" style="margin-top:10px">FILL THE FORM</span>
</section>

<div class="abs divider"></div>
<h3 class="abs blog-title" style="font-weight:400">LATEST FROM BLOG</h3>
<div class="abs arrows">
  <span><svg width="6" height="9" viewBox="0 0 6 9"><path d="M5 1L1.5 4.5 5 8" stroke="#fff" stroke-width="1.4" fill="none"/></svg></span>
  <span><svg width="6" height="9" viewBox="0 0 6 9"><path d="M1 1l3.5 3.5L1 8" stroke="#fff" stroke-width="1.4" fill="none"/></svg></span>
</div>
<div class="abs thumb" style="left:118px;background:linear-gradient(120deg,#dfe8ee,#9fc0d6)" role="img" aria-label="Blog photo: dentist examining a patient"></div>
<div class="abs thumb" style="left:269px;background:linear-gradient(160deg,#e6e8ea,#b9c2c8 60%,#2f6fb8)" role="img" aria-label="Blog photo: dental chair and equipment"></div>
<div class="abs thumb" style="left:422px;background:linear-gradient(180deg,#f3e9e4,#d9b3a8 50%,#c47f74)" role="img" aria-label="Blog photo: close-up of a smile with a dental mirror"></div>
<div class="abs thumb" style="left:574px;background:linear-gradient(120deg,#c7dced,#eef3f6 50%,#3a78b8)" role="img" aria-label="Blog photo: dentist standing behind a happy patient"></div>

<footer class="abs footer">
  <div class="footer-links">About Us<span>|</span>Advertise With Us<span>|</span>FAQ<span>|</span>Terms and Conditions<span>|</span>Privacy Policy<span>|</span>Contact Us</div>
  <div class="social" aria-label="Social network links"><span></span><span></span><span></span><span></span><span></span><span></span></div>
  <div class="copy">Copyright © 2014 . All Rights Reserved.</div>
</footer>
</body>
</html>
```